Need Primer (paint) Label Design

THE ATTACHED LABEL/S ARE SOLEY FOR REFERENCE. DO NOT MAKE ME AN INTERIOR PAINT OR CHALK PAINT LABEL. I ONLY NEED A "PRIMER" LABEL. THE ATTACHED INTERIOR PAINT LABEL IS ONLY TO SHOW YOU THE THEME/DESIGN OF OUR OTHER LABELS. THE BLUE LABEL ONLY HAS A DESIGN ASPECT I LIKE (PRIMER ON SIDE). The last four labels are our competitors.
```````````````````````````````````````````````````````````````````````````````````````````````````
We need this label to look professional, sharp, eye catching and modern.
OUR PRIMARY COLORS ARE BLACK AND WHITE. IF YOU INCOPORATE ANOTHER COLOR, SILVER OR GOLD MIGHT BE IDEAL BUT PLEASE DON'T DRIFT TOO FAR.
The attached documents:
1st - Our Logo
2nd - Our chalk paint label (reference). We do not need a chalk paint label.
3rd. A random design example. I like the PRIME on the side running vertically. I think it's a cool design concept.
````````````````````````````````````````````````````````````````````````````````````````````````````
We are going to be using a normal paint can with a metal bail/handle so please use that with you design work
``````````````````````````````````````````````````````````````````````````````````````````````````
Order, in my head:
4376
Coatings
^^ I want this to stand out as well but I don't want it to be the first thing your eye is drawn to. Probably 2nd
Interior/Exterior
Multi - Surface Primer
^^ Want this to stick out and draw your eye so the customer knows what it is immediately
Exceptional Adhesion, Performance, Durability,
Use on Wood, Drywall, Plaster, Stucco, Masonry, Brick, Paneling, Painted Metal, & Properly Prepared Glossy Surfaces & More
35* Lowe Temperature Application (can be on side or small)
100% Acrylic
Low Odor - Low VOC - Soap & Water Clean Up
1 US Gallon - 3.785 L
Feel free to get creative with it!

```html
<!DOCTYPE html>
<html lang="en">
<head>
<meta charset="utf-8">
<title>4376 Coatings — Multi-Surface Primer Label</title>
<link rel="stylesheet" href="https://fonts.googleapis.com/css2?family=Montserrat:wght@400;800;900&display=swap">
<style>
  :root {
    --paper: #f3f3f3;
    --ink: #1a1a1a;
    --ink-soft: #444444;
    --rule: #8a8a8a;
    --silver-light: #e4e4e4;
    --silver-mid: #bdbdbd;
    --silver-dark: #9a9a9a;
  }
  * { margin: 0; padding: 0; box-sizing: border-box; }
  html, body { width: 1200px; height: 863px; overflow: hidden; background: var(--paper); }
  .label {
    position: relative;
    width: 1200px;
    height: 863px;
    background: var(--paper);
    color: var(--ink);
    font-family: "Montserrat", sans-serif;
  }
  .brand {
    position: absolute; left: 230px; top: 170px; width: 400px;
    text-align: center; font-weight: 400; color: var(--ink);
    font-size: 52px; line-height: 1.1;
  }
  .use-zone { position: absolute; left: 230px; top: 310px; width: 400px; text-align: center;
    font-size: 40px; line-height: 1.25; font-weight: 400; letter-spacing: 1px; }
  .silver-panel {
    position: absolute; left: 660px; top: 460px; width: 330px; height: 280px;
    background: linear-gradient(100deg, var(--silver-light) 0%, var(--silver-mid) 55%, var(--silver-dark) 100%);
  }
  .product-main, .product-sub {
    position: absolute; writing-mode: vertical-rl; transform: rotate(180deg);
    white-space: nowrap; color: var(--ink);
  }
  .product-main { left: 870px; top: 140px; font-size: 112px; font-weight: 900; line-height: 1; letter-spacing: 2px; }
  .product-sub { left: 992px; top: 140px; font-size: 46px; font-weight: 800; line-height: 1; letter-spacing: 5px; }
  .divider { position: absolute; background: var(--rule); }
  .divider-a { left: 330px; top: 470px; width: 1px; height: 250px; }
  .divider-b { left: 650px; top: 470px; width: 1px; height: 250px; }
  .icons { position: absolute; left: 130px; top: 480px; width: 190px;
    display: grid; grid-template-columns: 1fr 1fr; row-gap: 26px; column-gap: 10px; }
  .icon { text-align: center; font-size: 10px; line-height: 1.25; color: var(--ink-soft); }
  .icon svg { display: block; margin: 0 auto 5px; }
  .temp-value { font-weight: 800; font-size: 20px; color: var(--ink); }
  .features { position: absolute; left: 340px; top: 500px; width: 300px; text-align: center; }
  .feature-list { font-size: 21px; line-height: 1.3; color: var(--ink-soft); }
  .resin { font-size: 21px; line-height: 1.25; color: var(--ink-soft); margin-top: 40px; }
  .specs { position: absolute; left: 672px; top: 484px; width: 186px; text-align: center; }
  .surfaces { font-size: 11px; line-height: 2.1; color: var(--ink-soft); }
  .volume { font-size: 18px; line-height: 1.25; color: var(--ink-soft); margin-top: 40px; letter-spacing: 1px; }
</style>
</head>
<body>
<main class="label">
  <div class="brand">4376<br>Coatings</div>

  <div class="use-zone">INTERIOR<br>EXTERIOR</div>

  <div class="silver-panel"></div>
  <div class="product-main">MULTI</div>
  <div class="product-sub">SURFACE PRIMER</div>

  <div class="divider divider-a"></div>
  <div class="divider divider-b"></div>

  <div class="icons">
    <div class="icon">
      <svg width="34" height="34" viewBox="0 0 34 34" fill="none" stroke="#1a1a1a" stroke-width="1.6">
        <path d="M17 6c-6 0-9 4-9 9 0 6 4 9 9 13 5-4 9-7 9-13 0-5-3-9-9-9z"/>
        <line x1="6" y1="28" x2="28" y2="6"/>
      </svg>
      Low Odor
    </div>
    <div class="icon">
      <svg width="34" height="34" viewBox="0 0 34 34" fill="none" stroke="#1a1a1a" stroke-width="1.6">
        <path d="M10 28c-4-6 4-10 0-18"/><path d="M17 28c-4-6 4-10 0-18"/><path d="M24 28c-4-6 4-10 0-18"/>
      </svg>
      Low VOC
    </div>
    <div class="icon">
      <svg width="34" height="34" viewBox="0 0 34 34" fill="none" stroke="#1a1a1a" stroke-width="1.6">
        <path d="M17 5c-4 6-7 10-7 14a7 7 0 0 0 14 0c0-4-3-8-7-14z"/>
        <circle cx="26" cy="8" r="2.5"/><circle cx="8" cy="9" r="1.8"/>
      </svg>
      Soap &amp; Water Clean Up
    </div>
    <div class="icon">
      <svg width="34" height="34" viewBox="0 0 34 34" fill="none" stroke="#1a1a1a" stroke-width="1.8">
        <rect x="14" y="4" width="6" height="20" rx="3"/><circle cx="17" cy="27" r="4.5"/>
        <line x1="17" y1="14" x2="17" y2="25"/>
      </svg>
      <span class="temp-value">35°</span><br>Low Temperature Application
    </div>
  </div>

  <div class="features">
    <div class="feature-list">Exceptional Adhesion<br>Performance<br>Durability</div>
    <div class="resin">100%<br>ACRYLIC</div>
  </div>

  <div class="specs">
    <div class="surfaces">Use on Wood, Drywall, Plaster, Stucco, Masonry, Brick, Paneling, Painted Metal, &amp; Properly Prepared Glossy Surfaces &amp; More</div>
    <div class="volume">1 US GALLON<br>3.785 L</div>
  </div>
</main>
</body>
</html>
```